Complete the Quillmark Holdings Inc. business card as started in the attached files.

See the attached card for the starting point.

Font is attached (File #3). The "F" box is a capital F on the font set, and the "Se" box is the number 4 on the font set.

I would like to see variations of the image provided (File #2). Image provided does not have proper balance of the boxes to the following letters (i.e. "F" is in a different plane than "uillmark", and "Se" is in the plane). Create the background to match the "drifting cold" example (File #1).

Completion of the work will be source files for TWO cards. One with no title under my name, and one with the title Junior Deputy Assistant to the Regional Associate Vice President.

With thanks,

Lou

Target Market(s)

Science nerds

Industry/Entity Type

Business

Requirements
Must have
• Green colour; if the background can match the pattern of the "drifting cold" background that is fantastic.
Must use the Font attached for the logo name. See notes in the brief.

```html
<!DOCTYPE html>
<html lang="en">
<head>
<meta charset="utf-8">
<title>Quillmark Holdings Inc. – Business Cards</title>
<link href="https://fonts.googleapis.com/css2?family=Open+Sans:wght@400;600;700&display=swap" rel="stylesheet">
<style>
  :root {
    --backdrop: #ededed;
    --card-green: #177a44;
    --ink-light: #eef3ee;
    --mark-fill: #cfe3d4;
  }
  html, body {
    margin: 0;
    width: 1200px;
    height: 1001px;
    overflow: hidden;
    background: var(--backdrop);
    font-family: "Open Sans", Arial, sans-serif;
  }
  .sheet {
    position: relative;
    width: 1200px;
    height: 1001px;
  }
  .card {
    position: absolute;
    top: 346px;
    width: 540px;
    height: 309px;
    background: var(--card-green);
    color: var(--ink-light);
    box-shadow: 0 2px 8px rgba(0,0,0,0.12);
  }
  .card--plain { left: 40px; }
  .card--titled { left: 620px; }

  .contact {
    position: absolute;
    left: 26px;
    top: 104px;
    font-size: 13px;
    font-weight: 600;
    line-height: 19px;
  }
  .brand {
    position: absolute;
    left: 190px;
    top: 30px;
    display: flex;
    align-items: flex-start;
    gap: 12px;
  }
  .brand__square {
    width: 44px;
    height: 44px;
    background: var(--mark-fill);
    flex: none;
    margin-top: 6px;
  }
  .brand__name {
    font-size: 42px;
    font-weight: 600;
    line-height: 46px;
    color: var(--ink-light);
    letter-spacing: 0.5px;
  }
  .person {
    position: absolute;
    left: 202px;
    top: 158px;
    text-align: center;
  }
  .person__name {
    font-size: 14px;
    font-weight: 700;
    letter-spacing: 0.3px;
  }
  .person__title {
    font-size: 9px;
    font-weight: 600;
    margin-top: 2px;
  }
  .address {
    position: absolute;
    left: 292px;
    top: 220px;
    font-size: 13px;
    font-weight: 600;
    line-height: 18px;
  }
  .address__company { font-weight: 700; font-size: 14px; }
</style>
</head>
<body>
<main class="sheet">

  <section class="card card--plain" aria-label="Business card without title">
    <div class="contact">
      <div>Ph: 780.555.0142</div>
      <div>lou@quillmark.ca</div>
      <div>www.quillmark.ca</div>
    </div>
    <div class="brand">
      <span class="brand__square"></span>
      <span class="brand__name">Quillmark<br>Holdings</span>
    </div>
    <div class="person">
      <div class="person__name">LEWIS HARTWELL</div>
    </div>
    <div class="address">
      <div class="address__company">Quillmark Holdings Inc.</div>
      <div>318, 40716 Range Road 117</div>
      <div>Maple Ridge, AB T4X 2K9</div>
    </div>
  </section>

  <section class="card card--titled" aria-label="Business card with title">
    <div class="contact">
      <div>Ph: 780.555.0142</div>
      <div>lou@quillmark.ca</div>
      <div>www.quillmark.ca</div>
    </div>
    <div class="brand">
      <span class="brand__square"></span>
      <span class="brand__name">Quillmark<br>Holdings</span>
    </div>
    <div class="person">
      <div class="person__name">LEWIS HARTWELL</div>
      <div class="person__title">Junior Deputy Assistant to the Associate Vice President</div>
    </div>
    <div class="address">
      <div class="address__company">Quillmark Holdings Inc.</div>
      <div>318, 40716 Range Road 117</div>
      <div>Maple Ridge, AB T4X 2K9</div>
    </div>
  </section>

</main>
</body>
</html>
```